Google Form Graphic to suit our Brand and industry

Create a graphic / image for us to put at the top of our client enquiry google form.
The image will be a section of an architectural home with our branding over the top. Preferably translucent.
The image must suit the shape of the google forms image, which is an elongated rectangle
#003d5d - brand colour

Target Market(s)

residential home owners, high end architectural homes

Industry/Entity Type

Residential construction

Colors
0054AA
0677BA
7BADD7
CADEEF
E8F1F8

Requirements
Must have
• our branding and a photo of an architectural home in the background

```html
<!DOCTYPE html>
<html lang="en">
<head>
<meta charset="utf-8">
<title>New Client Enquiry Form</title>
<link rel="stylesheet" href="https://fonts.googleapis.com/css2?family=Roboto:wght@400;500&family=Varela+Round&display=swap">
<style>
  :root {
    --brand-navy: #003d5d;
    --page-grey: #e6e6e6;
    --form-cream: #f5eedd;
    --card-white: #ffffff;
    --card-border: #dadce0;
    --text-dark: #202124;
    --text-muted: #70757a;
    --focus-blue: #4285f4;
    --required-red: #d93025;
    --section-gold: #e0b25a;
  }
  * { box-sizing: border-box; margin: 0; padding: 0; }
  html, body { width: 937px; height: 1200px; overflow: hidden; }
  body {
    position: relative;
    background: var(--page-grey);
    font-family: "Roboto", Arial, sans-serif;
    color: var(--text-dark);
  }
  .form-column {
    position: absolute; left: 96px; top: 0; width: 754px; height: 1200px;
    background: var(--form-cream);
  }
  .header-banner {
    position: absolute; left: 127px; top: 10px; width: 702px; height: 260px;
  }
  .header-banner svg { display: block; }
  .brand-mark {
    position: absolute; left: 26px; top: 96px;
    display: flex; align-items: center; gap: 10px;
  }
  .brand-square {
    width: 14px; height: 14px; background: var(--card-white);
  }
  .brand-name {
    font-family: "Varela Round", Arial, sans-serif;
    font-size: 25px; line-height: 33px; color: var(--card-white);
  }
  .banner-tagline {
    position: absolute; right: 23px; top: 86px; text-align: right;
    font-family: "Varela Round", Arial, sans-serif;
    font-size: 25px; line-height: 33px; color: var(--card-white);
  }
  .section-tab {
    position: absolute; left: 127px; top: 284px; height: 42px; padding: 0 11px;
    background: var(--brand-navy); color: var(--card-white);
    font-family: "Varela Round", Arial, sans-serif; font-size: 17px;
    display: flex; align-items: center; border-radius: 6px 6px 0 0;
  }
  .section-rule {
    position: absolute; left: 127px; top: 325px; width: 702px; height: 11px;
    background: var(--brand-navy);
  }
  .card {
    position: absolute; left: 127px; width: 702px;
    background: var(--card-white); border: 1px solid var(--card-border); border-radius: 10px;
  }
  .title-card { top: 335px; height: 196px; border-top: none; border-radius: 0 0 10px 10px; }
  .form-title {
    position: absolute; left: 23px; top: 64px; width: 580px;
    font-size: 29px; font-weight: 400; padding-bottom: 7px; border-bottom: 1px solid #5f6368;
  }
  .title-tools { position: absolute; right: 30px; top: 65px; display: flex; gap: 30px; color: #5f6368; font-size: 18px; }
  .format-bar { position: absolute; left: 33px; top: 117px; display: flex; gap: 22px; align-items: center; color: #5f6368; }
  .format-bar b, .format-bar i, .format-bar u { font-size: 15px; font-weight: 600; }
  .form-description { position: absolute; left: 23px; top: 154px; font-size: 13px; }
  .question-card { height: 125px; }
  .question-card.is-active { border-left: 6px solid var(--focus-blue); }
  .question-label { position: absolute; left: 23px; top: 26px; font-size: 15px; }
  .is-active .question-label { left: 26px; }
  .required { color: var(--required-red); margin-left: 6px; }
  .answer-line {
    position: absolute; left: 23px; top: 62px; width: 330px;
    font-size: 12px; color: var(--text-muted); padding-bottom: 5px;
    border-bottom: 1px dotted #9aa0a6;
  }
  .is-active .answer-line { left: 17px; }
  .section-routing { position: absolute; left: 127px; top: 1098px; font-size: 12.5px; display: flex; align-items: center; gap: 16px; }
  .routing-caret { margin-left: 128px; font-size: 10px; color: #5f6368; }
  .side-toolbar { position: absolute; left: 839px; top: 1099px; width: 14px; height: 101px; background: var(--card-white); border-radius: 6px 0 0 0; }
  .next-section-tab {
    position: absolute; left: 127px; top: 1169px; height: 40px; padding: 0 11px 8px;
    background: var(--section-gold); border-radius: 6px 6px 0 0;
    font-size: 13px; display: flex; align-items: center;
  }
</style>
</head>
<body>
  <div class="form-column"></div>

  <header class="header-banner">
    <svg width="702" height="260" viewBox="0 0 702 260" role="img" aria-label="Photo of a covered architectural outdoor living area with lounge and dining furniture, under a translucent navy tint">
      <defs>
        <linearGradient id="photoTone" x1="0" y1="0" x2="1" y2="1">
          <stop offset="0" stop-color="#5f7f97"/>
          <stop offset="0.5" stop-color="#8ea6b8"/>
          <stop offset="1" stop-color="#3f5f78"/>
        </linearGradient>
      </defs>
      <rect width="702" height="260" fill="url(#photoTone)"/>
      <polygon points="0,238 351,215 702,238 702,260 0,260" fill="#5f7f97"/>
      <polygon points="0,248 351,222 702,243 702,250 351,232 0,260" fill="#003d5d"/>
    </svg>
    <div class="brand-mark">
      <span class="brand-square"></span>
      <span class="brand-name">Arvo</span>
    </div>
    <div class="banner-tagline">Custom Home Construction<br>– Built With You</div>
  </header>

  <div class="section-tab">Section 1 of 4</div>
  <div class="section-rule"></div>

  <section class="card title-card">
    <h1 class="form-title">New Client Enquiry Form</h1>
    <div class="title-tools"><span>⌅</span><span>⋮</span></div>
    <div class="format-bar">
      <b>B</b><i>I</i><u>U</u>
      <svg width="16" height="10" viewBox="0 0 16 10"><rect x="1" y="1" width="14" height="8" rx="4" fill="none" stroke="#5f6368" stroke-width="1.8"/><line x1="5" y1="5" x2="11" y2="5" stroke="#5f6368" stroke-width="1.8"/></svg>
      <svg width="14" height="14" viewBox="0 0 14 14"><path d="M2 2h10M7 2L5 12M9 9l4 4M13 9l-4 4" stroke="#5f6368" stroke-width="1.6" fill="none"/></svg>
    </div>
    <p class="form-description">We would love to hear your thoughts or feedback on how we can improve your experience!</p>
  </section>

  <section class="card question-card is-active" style="top:544px">
    <p class="question-label">Firstly, how did you hear about us?<span class="required">*</span></p>
    <p class="answer-line">Short answer text</p>
  </section>

  <section class="card question-card" style="top:682px">
    <p class="question-label">Name</p>
    <p class="answer-line">Short answer text</p>
  </section>

  <section class="card question-card" style="top:820px">
    <p class="question-label">Phone</p>
    <p class="answer-line">Short answer text</p>
  </section>

  <section class="card question-card" style="top:956px">
    <p class="question-label">Email</p>
    <p class="answer-line">Short answer text</p>
  </section>

  <div class="section-routing">
    <span>After section 1</span><span>Continue to next section</span><span class="routing-caret">▼</span>
  </div>
  <div class="side-toolbar"></div>

  <div class="next-section-tab">Section 2 of 4</div>
</body>
</html>
```